New Dynamic Design Based on Other Site

We need a new website designed where the front page is VERY SEO Friendly. The front page should almost follow the same SEO principles that are on RankLoomPress.com. The inner pages need to follow the same exact video animations that occur on vollq.com. I'd like to keep our "marbletons" theme throughout the new design but we will provide all of the content but I want someone to design something SEO friendly, new blog theme, and actual inner pages that are dynamic and based on those short videos.

Check attached file for company name and site that we currently have. Feel free to pull the content from that site and re-use it and also leave placeholders for the rest of them.

PLEASE NO USE OF STOCK IMAGES. Use a designer or an illustrator to create the various images.

Please make sure the front page is SEO friendly! Make sure you familiarize yourself with the quorvix algorithm for SEO. Content above the fold H1 Tags Very mobile friendly Minimal javascript and animations Basically a quality static page with optimized content

Target Market(s)

call center companies, anything call related

Industry/Entity Type

Telecommunications

Number of Pages Required

4 page

Font styles to use
Sans Serif

Colors
33a6d7
85cae6
0792cd
0255a3
cee9f5
ecf7fb
ffffff

Requirements
Must have
• places for video animations
• dynamic functionality
• SEO friendly (front page)
Should not have
• should not look like a template. needs to be unique

```html
<!DOCTYPE html>
<html lang="en">
<head>
<meta charset="utf-8">
<title>DialMetric — Call Quality Monitoring</title>
<link href="https://fonts.googleapis.com/css2?family=Montserrat:wght@400;600;700&family=Open+Sans:wght@400;600;700&display=swap" rel="stylesheet">
<style>
:root{
  --blue:#0792cd;
  --sky:#33a6d7;
  --light:#85cae6;
  --navy:#0255a3;
  --pale:#cee9f5;
  --mist:#ecf7fb;
  --white:#ffffff;
  --ink:#2b3a48;
  --muted:#8a97a3;
  --footer:#2b2e34;
  --footer-deep:#222429;
  --line:#e3e9ee;
}
*{box-sizing:border-box;margin:0;padding:0}
html,body{width:1200px;height:3448px;overflow:hidden}
body{font-family:"Open Sans",Arial,sans-serif;color:var(--ink);background:var(--white);font-size:13px;line-height:1.7}
h1,h2,h3,h4{font-family:"Montserrat",Arial,sans-serif;font-weight:700}
section{overflow:hidden}
.wrap{width:1000px;margin:0 auto;position:relative}
.btn{display:inline-block;font-family:"Montserrat",sans-serif;font-size:11px;font-weight:600;letter-spacing:1px;padding:10px 26px;border-radius:3px;text-transform:uppercase;line-height:1.4}
.btn-solid{background:var(--navy);color:var(--white)}
.btn-ghost{border:1px solid var(--white);color:var(--white)}
.btn-blue{background:var(--blue);color:var(--white)}
.brand{font-family:"Open Sans",sans-serif;font-weight:700;font-size:26px;color:var(--navy);display:flex;align-items:center;gap:10px}
.brand-dot{width:30px;height:30px;border-radius:50%;background:var(--sky)}

/* top bar */
.topbar{height:32px;background:var(--white);border-bottom:1px solid var(--line);font-size:11px;color:var(--muted)}
.topbar .wrap{display:flex;gap:30px;align-items:center;height:32px}
/* nav */
.nav{height:72px;background:var(--white);box-shadow:0 2px 6px rgba(0,0,0,.05);position:relative;z-index:2}
.nav .wrap{display:flex;align-items:center;justify-content:space-between;height:72px}
.menu{display:flex;gap:4px;list-style:none}
.menu li{font-family:"Montserrat",sans-serif;font-size:10px;font-weight:600;letter-spacing:.5px;color:var(--ink);padding:8px 12px}
.menu li.active{background:var(--blue);color:var(--white)}

/* hero */
.hero{height:424px;background:linear-gradient(180deg,var(--blue),var(--sky));color:var(--white);position:relative}
.hero .wrap{height:424px}
.hero-text{position:absolute;left:0;top:86px;width:420px}
.hero-kicker{font-size:13px;font-weight:600;letter-spacing:1px;margin-bottom:6px}
.hero h1{font-size:34px;line-height:1.15;margin-bottom:18px}
.hero p{font-size:12px;opacity:.9;margin-bottom:26px}
.hero-art{position:absolute;right:0;top:40px;width:540px;height:330px;border-radius:6px;background:radial-gradient(ellipse at 55% 50%,#e9f4fa 0%,#b9dcee 45%,rgba(133,202,230,0) 72%)}
.dots{position:absolute;bottom:18px;left:50%;transform:translateX(-50%);display:flex;gap:8px}
.dots span{width:7px;height:7px;border-radius:50%;background:rgba(255,255,255,.5)}
.dots span:first-child{background:var(--white)}

/* welcome */
.welcome{height:360px;background:var(--mist);text-align:center;padding-top:62px}
.sec-title{font-size:24px;color:var(--ink);margin-bottom:22px;letter-spacing:.5px;line-height:1.3}
.sec-title em{font-style:normal;color:var(--sky)}
.welcome p{width:820px;margin:0 auto 14px;font-size:11.5px;color:var(--muted)}
.welcome .btn{margin-top:10px}

/* features */
.features{height:340px;padding-top:86px}
.features .wrap{display:flex;justify-content:space-between;width:860px}
.feature{width:250px;text-align:center}
.feature svg{width:46px;height:46px;margin-bottom:10px}
.feature h3{font-size:14px;margin-bottom:10px;color:var(--ink)}
.feature p{font-size:11.5px;color:var(--muted)}

/* why */
.why{height:280px;background:var(--mist);position:relative}
.why-map{position:absolute;left:60px;top:20px;width:640px;height:240px;background:radial-gradient(ellipse,rgba(133,202,230,.35),rgba(236,247,251,0) 70%)}
.why-art{position:absolute;left:200px;top:52px;width:320px;height:180px;border-radius:6px;background:linear-gradient(180deg,#ffffff,var(--pale))}
.accordion{position:absolute;left:640px;top:40px;width:440px}
.acc-head{display:flex;justify-content:space-between;align-items:center;background:var(--white);border:1px solid var(--line);padding:8px 12px;font-size:12px;font-weight:600;margin-bottom:8px}
.acc-head i{width:18px;height:18px;background:var(--navy);color:var(--white);font-style:normal;font-size:12px;line-height:18px;text-align:center}
.acc-body{font-size:11px;color:var(--muted);padding:2px 12px 14px}

/* ut wisi */
.intro{height:200px;text-align:center;padding-top:58px}
.intro p{width:620px;margin:0 auto;font-size:11.5px;color:var(--muted)}

/* tiles */
.tiles{height:272px;display:flex}
.tile{flex:1;position:relative;color:var(--white)}
.tile:nth-child(1){background:var(--blue)}
.tile:nth-child(2){background:var(--sky)}
.tile:nth-child(3){background:var(--blue)}
.tile:nth-child(4){background:var(--light)}
.tile-art{position:absolute;left:85px;top:60px;width:130px;height:110px;border-radius:6px;background:rgba(255,255,255,.18)}
.tile-cap{position:absolute;left:0;right:0;bottom:40px;text-align:center;font-size:11px;font-weight:600}

/* newsletter */
.newsletter{height:68px;background:var(--navy);color:var(--white)}
.newsletter .wrap{display:flex;align-items:center;justify-content:center;gap:40px;height:68px}
.newsletter h4{font-size:14px;letter-spacing:1px}
.newsletter .field{width:150px;height:30px;border:1px solid var(--white);font-size:10px;text-align:center;line-height:28px;letter-spacing:1px}

/* pricing */
.pricing{height:552px;text-align:center;padding-top:48px}
.pricing .sec-title{margin-bottom:16px}
.pricing .lead{width:620px;margin:0 auto 28px;font-size:11.5px;color:var(--muted)}
.plans{display:flex;justify-content:center;align-items:flex-start}
.plan{width:190px;background:var(--white);border:1px solid var(--line);margin-top:20px}
.plan.featured{margin-top:0;box-shadow:0 6px 18px rgba(2,85,163,.18);position:relative;z-index:1}
.plan-head{background:var(--light);color:var(--white);font-family:"Montserrat",sans-serif;font-size:10px;font-weight:600;letter-spacing:1px;padding:6px;line-height:1.6}
.featured .plan-head{background:var(--navy);padding:12px}
.price{padding:18px 0 12px;background:var(--mist);line-height:1}
.price b{font-family:"Montserrat",sans-serif;font-size:42px;color:var(--ink);line-height:1}
.price sup{font-size:18px;vertical-align:top}
.price small{display:block;font-size:10px;color:var(--muted);margin-top:4px}
.plan ul{list-style:none;font-size:10.5px;line-height:1.6;color:var(--muted);padding:8px 0}
.plan li{padding:3px 0}
.plan .btn{margin-bottom:16px;padding:7px 22px;font-size:9px}

/* video */
.video{height:408px;display:flex}
.video-text{width:440px;background:#eef0f2;padding:90px 60px 0 100px}
.video-text h2{font-size:24px;margin-bottom:18px}
.video-text p{font-size:11px;color:var(--muted);margin-bottom:12px}
.video-stage{flex:1;background:linear-gradient(135deg,var(--sky),var(--blue));position:relative}
.video-art{position:absolute;left:90px;top:60px;width:520px;height:290px;border-radius:8px;background:linear-gradient(180deg,#e8f4fa,var(--pale))}
.play{position:absolute;left:320px;top:175px;width:56px;height:56px}

/* footer */
.footer{height:440px;background:var(--footer);color:#aeb4ba;position:relative}
.footer .wrap{display:flex;padding-top:48px}
.f-col h4{font-size:11px;color:var(--white);letter-spacing:1px;margin-bottom:8px;padding-bottom:8px;border-bottom:1px solid #3d4148}
.f-brand{width:360px;padding-top:46px}
.f-brand .brand{color:var(--white);font-size:30px;margin-bottom:20px}
.f-brand p{font-size:11px;line-height:2}
.f-links{width:320px}
.f-links li{list-style:none;font-size:11px;padding:6px 0;border-bottom:1px solid #35393f}
.f-posts{width:320px}
.post{display:flex;gap:12px;margin-bottom:16px;font-size:11px}
.post svg{flex:none;width:28px;height:28px}
.post small{display:block;font-size:9.5px;color:#7c838a}
.copy{position:absolute;left:0;right:0;bottom:0;height:36px;background:var(--footer-deep);font-size:10px}
.copy .wrap{display:flex;justify-content:space-between;align-items:center;height:36px;padding-top:0}
.social{display:flex;gap:8px}
.social span{width:8px;height:8px;background:#6d737a}
</style>
</head>
<body>

<header>
  <div class="topbar"><div class="wrap"><span>hello@dialmetric.com</span><span>(555) 013-0420</span></div></div>
  <nav class="nav"><div class="wrap">
    <div class="brand"><span class="brand-dot"></span>DialMetric</div>
    <ul class="menu">
      <li class="active">HOME</li><li>SERVICES</li><li>EXTERNAL REVIEWS</li><li>SCORECARD REVIEWS</li><li>PRICING</li><li>BLOG</li><li>CONTACT US</li>
    </ul>
  </div></nav>
</header>

<main>
<section class="hero"><div class="wrap">
  <div class="hero-text">
    <div class="hero-kicker">HELLO, ARE YOU READY TO START ?</div>
    <h1>LOREM &amp; DOLOR<br>SIT AMET NONUMMY</h1>
    <p>Aliquam consectetuer nisl sapien vel sollicitudin. Sed tincidunt commodo tellus, sed et volutpat augue tincidunt vel. Suspendisse suscipit id ligula eu dictum.</p>
    <a class="btn btn-solid">Free Quote</a>&nbsp;&nbsp;<a class="btn btn-ghost">Read More</a>
  </div>
  <div class="hero-art" role="img" aria-label="Illustration of laptop and desktop screens showing call analytics dashboards"></div>
  <div class="dots"><span></span><span></span><span></span></div>
</div></section>

<section class="welcome">
  <h2 class="sec-title">WELCOME TO DIAL<em>METRIC</em></h2>
  <p>Nulla facilisi morbi tempus iaculis urna id volutpat lacus laoreet non curabitur gravida. Vitae tempus quam pellentesque nec nam aliquam sem et tortor. Consequat semper viverra nam libero justo laoreet sit amet cursus sit amet dictum. Amet porttitor eget dolor morbi non arcu risus quis varius quam quisque id diam vel quam elementum pulvinar etiam non quam lacus.</p>
  <p>Aliquam purus sit amet luctus venenatis lectus magna fringilla urna porttitor rhoncus dolor purus non enim. Praesent elementum facilisis leo vel fringilla est ullamcorper eget nulla facilisi etiam dignissim diam quis enim lobortis scelerisque. Fermentum dui faucibus in ornare quam viverra orci sagittis eu volutpat odio facilisis mauris sit amet massa vitae tortor.</p>
  <a class="btn btn-blue">Read More</a>
</section>

<section class="features"><div class="wrap">
  <div class="feature">
    <svg viewBox="0 0 46 46" fill="none" stroke="#0792cd" stroke-width="2"><rect x="6" y="10" width="34" height="24" rx="2"/><path d="M14 26l6-7 6 4 8-9"/><path d="M18 40h10M23 34v6"/></svg>
    <h3>Dolore magna aliquam</h3>
    <p>Lorem ipsum dolor sit amet consectetuer adipiscing elit sed diam nonummy nibh euismod tincidunt ut laoreet dolore magna aliquam erat volutpat.</p>
  </div>
  <div class="feature">
    <svg viewBox="0 0 46 46" fill="none" stroke="#0792cd" stroke-width="2"><path d="M5 9h6l5 20h20l4-14H13"/><circle cx="19" cy="36" r="3"/><circle cx="33" cy="36" r="3"/></svg>
    <h3>Dolore magna aliquam</h3>
    <p>Lorem ipsum dolor sit amet consectetuer adipiscing elit sed diam nonummy nibh euismod tincidunt ut laoreet dolore magna aliquam erat volutpat.</p>
  </div>
  <div class="feature">
    <svg viewBox="0 0 46 46" fill="none" stroke="#0792cd" stroke-width="2"><rect x="5" y="8" width="24" height="16" rx="2"/><path d="M11 24v6l6-6"/><rect x="19" y="20" width="22" height="14" rx="2"/><path d="M35 34v5l-5-5"/></svg>
    <h3>Dolore magna aliquam</h3>
    <p>Lorem ipsum dolor sit amet consectetuer adipiscing elit sed diam nonummy nibh euismod tincidunt ut laoreet dolore magna aliquam erat volutpat.</p>
  </div>
</div></section>

<section class="why">
  <div class="why-map" role="img" aria-label="Faint world map in the background"></div>
  <div class="why-art" role="img" aria-label="Illustration of a laptop showing a call review report"></div>
  <div class="accordion">
    <div class="acc-head">Why Choose Us <i>−</i></div>
    <p class="acc-body">Ut wisi enim ad minim veniam, quis nostrud exerci tation ullamcorper suscipit lobortis nisl ut aliquip ex ea commodo consequat. Duis autem vel eum iriure dolor in hendrerit in vulputate velit esse molestie consequat, vel illum dolore eu feugiat nulla.</p>
    <div class="acc-head">Powerful Analytics <i>+</i></div>
    <div class="acc-head">24/7 Expert Support <i>+</i></div>
  </div>
</section>

<section class="intro">
  <h2 class="sec-title">UT WISI ENIM AD MINIM VENIAM</h2>
  <p>Nam liber tempor cum soluta nobis eleifend option congue nihil imperdiet doming id quod mazim placerat facer possim assum. Typi non habent claritatem insitam est usus legentis in iis.</p>
</section>

<section class="tiles">
  <div class="tile"><div class="tile-art" role="img" aria-label="Illustration of a handshake"></div><div class="tile-cap">Trusted Partners</div></div>
  <div class="tile"><div class="tile-art" role="img" aria-label="Illustration of a rising bar chart"></div><div class="tile-cap">Growth Reports</div></div>
  <div class="tile"><div class="tile-art" role="img" aria-label="Illustration of a monitoring dashboard"></div><div class="tile-cap">Live Dashboards</div></div>
  <div class="tile"><div class="tile-art" role="img" aria-label="Illustration of a call center agent"></div><div class="tile-cap">Expert Reviewers</div></div>
</section>

<section class="newsletter"><div class="wrap">
  <h4>JOIN OUR LATEST NEWSLETTER</h4>
  <div class="field">SUBSCRIBE NOW</div>
</div></section>

<section class="pricing">
  <h2 class="sec-title">PRICING</h2>
  <p class="lead">Duis autem vel eum iriure dolor in hendrerit in vulputate velit esse molestie consequat, vel illum dolore eu feugiat nulla facilisis at vero eros et accumsan.</p>
  <div class="plans">
    <div class="plan">
      <div class="plan-head">BASIC</div>
      <div class="price"><b><sup>$</sup>12</b><small>per month</small></div>
      <ul><li>Call Monitoring</li><li>Weekly Reports</li><li>Email Support</li><li>Custom Scorecards</li><li>50 Calls Reviewed</li><li>Single User</li></ul>
      <a class="btn btn-blue">Sign Up</a>
    </div>
    <div class="plan featured">
      <div class="plan-head">STANDARD</div>
      <div class="price"><b><sup>$</sup>59</b><small>per month</small></div>
      <ul><li>Call Monitoring</li><li>Daily Reports</li><li>Phone Support</li><li>Custom Scorecards</li><li>500 Calls Reviewed</li><li>Five Users</li></ul>
      <a class="btn btn-blue">Sign Up</a>
    </div>
    <div class="plan">
      <div class="plan-head">PREMIUM</div>
      <div class="price"><b><sup>$</sup>79</b><small>per month</small></div>
      <ul><li>Call Monitoring</li><li>Live Reports</li><li>Priority Support</li><li>Custom Scorecards</li><li>Unlimited Calls</li><li>Unlimited Users</li></ul>
      <a class="btn btn-blue">Sign Up</a>
    </div>
  </div>
</section>

<section class="video">
  <div class="video-text">
    <h2>WATCH OUR VIDEO</h2>
    <p>Claritas est etiam processus dynamicus, qui sequitur mutationem consuetudium lectorum. Mirum est notare quam littera gothica, quam nunc putamus parum claram, anteposuerit litterarum formas humanitatis.</p>
    <p>Eodem modo typi, qui nunc nobis videntur parum clari, fiant sollemnes in futurum. Investigationes demonstraverunt lectores legere me lius quod ii legunt saepius.</p>
    <a class="btn btn-blue">Read More</a>
  </div>
  <div class="video-stage">
    <div class="video-art" role="img" aria-label="Illustration of a laptop playing a product video"></div>
    <svg class="play" viewBox="0 0 56 56"><circle cx="28" cy="28" r="26" fill="#0792cd"/><path d="M23 18l15 10-15 10z" fill="#fff"/></svg>
  </div>
</section>
</main>

<footer class="footer">
  <div class="wrap">
    <div class="f-col f-brand">
      <div class="brand"><span class="brand-dot"></span>DialMetric</div>
      <p>12 Harbor Lane, Suite 4<br>(555) 013-0420<br>hello@dialmetric.com</p>
    </div>
    <div class="f-col f-links">
      <h4>SITE LINKS</h4>
      <ul><li>Home</li><li>Services</li><li>Scorecard Reviews</li><li>External Reviews</li><li>Pricing</li><li>Blog</li><li>Contact Us</li></ul>
    </div>
    <div class="f-col f-posts">
      <h4>RECENT POSTS</h4>
      <div class="post"><svg viewBox="0 0 28 28" fill="none" stroke="#aeb4ba" stroke-width="1.6"><path d="M6 22l3-1 12-12-2-2L7 19z"/></svg><div>How scorecards raise agent quality each week<small>12 March 2024</small></div></div>
      <div class="post"><svg viewBox="0 0 28 28" fill="none" stroke="#aeb4ba" stroke-width="1.6"><path d="M6 22l3-1 12-12-2-2L7 19z"/></svg><div>Five metrics every call team should track<small>04 March 2024</small></div></div>
      <div class="post"><svg viewBox="0 0 28 28" fill="none" stroke="#aeb4ba" stroke-width="1.6"><path d="M6 22l3-1 12-12-2-2L7 19z"/></svg><div>Turning recorded calls into clear coaching plans<small>26 February 2024</small></div></div>
    </div>
  </div>
  <div class="copy"><div class="wrap">
    <span>© 2024 DialMetric. All rights reserved.</span>
    <div class="social"><span></span><span></span><span></span><span></span></div>
  </div></div>
</footer>

</body>
</html>
```